Elevating our current Business Card Design

We want to elevate our current business card with a new design to look like a zenith 300 company. We are a premium lubricant distributor (oil and grease).
We need 2 versions, version 1 is as per the uploaded a copy of our current business card with the English version.
For our Chinese version we need to use the front to be English in English and have the back of the card designed exactly like the front for all info to be in Chinese.
The design template needs to be such that we can amend the template with adding different information for each person's card.
The background colour of the card can be changed- we just need to clearly see all information on the card and logos.
The QJR and Ember steady logos cannot have any colour or display changes- only use the logos attached.
All logos need to be included and all information from the attached current card

```html
<!DOCTYPE html>
<html lang="en">
<head>
<meta charset="utf-8">
<title>Orvane Business Card</title>
<link rel="stylesheet" href="https://fonts.googleapis.com/css2?family=Open+Sans:wght@400;600;700;800&display=swap">
<style>
  :root {
    --stage: #222222;
    --card-white: #ffffff;
    --forest: #06301f;
    --signal-red: #e8302a;
    --ink-white: #ffffff;
    --gold: #e0a82e;
    --badge-orange: #ee7a22;
    --badge-grey: #9a9a9a;
    --text-font: "Open Sans", Arial, sans-serif;
  }
  * { box-sizing: border-box; margin: 0; padding: 0; }
  html, body {
    width: 1200px; height: 780px; overflow: hidden;
    background: var(--stage);
    font-family: var(--text-font);
  }
  .stage {
    position: relative; width: 1200px; height: 780px;
    display: flex; align-items: center; justify-content: center; gap: 40px;
  }
  .card {
    position: relative; width: 540px; height: 320px; overflow: hidden;
    box-shadow: 0 10px 24px rgba(0,0,0,.45);
  }

  /* Front */
  .card-front {
    background: var(--card-white);
    display: flex; align-items: center; justify-content: center; gap: 18px;
  }
  .brand-dot {
    width: 46px; height: 46px; border-radius: 50%; background: var(--gold);
  }
  .brand-name {
    font-size: 84px; font-weight: 800; color: var(--signal-red);
    letter-spacing: -1px; line-height: 1;
  }

  /* Back */
  .card-back { background: var(--forest); display: flex; }
  .partner-strip {
    position: relative; width: 124px; height: 100%;
    background: var(--card-white); flex: none;
  }
  .partner-strip-inner {
    position: absolute; width: 320px; height: 124px;
    left: 124px; top: 0;
    transform-origin: 0 0; transform: rotate(90deg);
  }
  .network-member {
    position: absolute; left: 12px; top: 10px;
    display: flex; align-items: center; gap: 5px;
    white-space: nowrap;
  }
  .network-member .mark {
    width: 18px; height: 18px; border-radius: 50%; background: var(--forest); flex: none;
  }
  .network-member .name {
    font-size: 9px; font-weight: 700; color: var(--forest); line-height: 1.15;
  }
  .cert-badges {
    position: absolute; left: 134px; top: 8px; display: flex; gap: 22px;
  }
  .cert-badge {
    width: 34px; height: 34px; border-radius: 50%;
    background: var(--badge-orange); border: 4px solid var(--badge-grey);
  }
  .distributor-box {
    position: absolute; left: 10px; top: 58px; width: 126px; height: 58px;
    border: 2px solid var(--signal-red); border-right: none;
    border-radius: 4px 0 0 4px; padding: 6px 8px;
  }
  .distributor-box .name {
    font-size: 18px; font-weight: 800; color: var(--signal-red); line-height: 1;
  }
  .distributor-box .tagline {
    margin-top: 4px; font-size: 7.5px; color: var(--signal-red);
    text-transform: uppercase; line-height: 1.15;
  }
  .supplier-band {
    position: absolute; left: 136px; top: 58px; width: 168px; height: 58px;
    background: var(--signal-red); border-radius: 0 0 12px 0;
    color: var(--ink-white); padding: 8px 12px;
  }
  .supplier-band .name {
    font-size: 20px; font-weight: 800; letter-spacing: 1px; line-height: 1.05;
  }
  .supplier-band .tagline {
    font-size: 9px; font-weight: 600; letter-spacing: .8px; text-transform: uppercase;
  }

  .contact-panel {
    position: relative; flex: 1; padding: 34px 40px 0 0;
    text-align: right; color: var(--ink-white);
  }
  .name-tab {
    position: absolute; right: 0; top: 36px; width: 14px; height: 42px;
    background: var(--signal-red);
  }
  .person-name {
    font-size: 27px; font-weight: 700; color: var(--signal-red); line-height: 1.1;
  }
  .person-role { font-size: 14px; font-weight: 600; margin-top: 2px; }
  .address { margin-top: 14px; font-size: 13px; line-height: 1.4; }
  .contact-list { list-style: none; margin-top: 14px; font-size: 13px; }
  .contact-list li {
    display: flex; justify-content: flex-end; align-items: center; gap: 8px;
    line-height: 1.55;
  }
  .contact-list svg { width: 13px; height: 13px; flex: none; }
</style>
</head>
<body>
<main class="stage">

  <section class="card card-front" aria-label="Card front">
    <span class="brand-dot" aria-hidden="true"></span>
    <span class="brand-name">Orvane</span>
  </section>

  <section class="card card-back" aria-label="Card back">
    <aside class="partner-strip">
      <div class="partner-strip-inner">
        <div class="network-member">
          <span class="mark" aria-hidden="true"></span>
          <span class="name">Ember steady<br>network member</span>
        </div>
        <div class="cert-badges" aria-label="QJR certifications">
          <span class="cert-badge"></span>
          <span class="cert-badge"></span>
          <span class="cert-badge"></span>
        </div>
        <div class="distributor-box">
          <div class="name">Orvane</div>
          <div class="tagline">Orvane lubricant<br>distributors</div>
        </div>
        <div class="supplier-band">
          <div class="name">KESTREL</div>
          <div class="tagline">Premium lubricants</div>
        </div>
      </div>
    </aside>

    <div class="contact-panel">
      <span class="name-tab" aria-hidden="true"></span>
      <h1 class="person-name">Mara Delton</h1>
      <p class="person-role">Administration Executive</p>
      <p class="address">48 Freight Avenue<br>Hollis, WA 6112</p>
      <ul class="contact-list">
        <li>1300 482 716
          <svg viewBox="0 0 16 16" aria-hidden="true"><path fill="#e8302a" d="M3 1l3 3-2 2c1 2 3 4 5 5l2-2 3 3-2 2C7 14 2 9 1 3z"/></svg></li>
        <li>+61 400 218 935
          <svg viewBox="0 0 16 16" aria-hidden="true"><rect x="4" y="1" width="8" height="14" rx="1.5" fill="none" stroke="#e8302a" stroke-width="1.6"/></svg></li>
        <li>+61 8 9000 4412
          <svg viewBox="0 0 16 16" aria-hidden="true"><rect x="1" y="6" width="14" height="9" rx="1" fill="#e8302a"/><rect x="4" y="1" width="8" height="5" fill="#e8302a"/></svg></li>
        <li>www.orvanedirect.com
          <svg viewBox="0 0 16 16" aria-hidden="true"><circle cx="8" cy="8" r="6.5" fill="none" stroke="#e8302a" stroke-width="1.6"/><path d="M1.5 8h13M8 1.5c3 3 3 10 0 13M8 1.5c-3 3-3 10 0 13" fill="none" stroke="#e8302a" stroke-width="1.2"/></svg></li>
        <li>mara.delton@orvanedirect.com
          <svg viewBox="0 0 16 16" aria-hidden="true"><rect x="1" y="3" width="14" height="10" rx="1" fill="#e8302a"/><path d="M1.5 4l6.5 5 6.5-5" fill="none" stroke="#06301f" stroke-width="1.2"/></svg></li>
      </ul>
    </div>
  </section>

</main>
</body>
</html>
```